The Moss Hollow Organic & Natural Soaps is looking for label designs (along with the business card proje

This is my scope and requirements:
Labelling project:
This is related to the Label project I also opened up. (The Moss Hollow Organic & Natural Soaps needs a good business card (Contest) )
I have attached an initial draft at a logo I tried to come up with for a business card and labelling/marketing. I am hoping that you can take this logo and 'run with it' to finesse it, make it look unique and professional. If you need to change it, I am open to ideas.
I find that labelling/packaging is hard for me to make it look 'professional' so I am coming to the experts!
I am looking for label designs for 2 different bottles and 2 different bar soaps:
1) Organic Bar Soap (2 possibilities: 1) Kraft 'cigar' band around soap with twine, 2) Kraft soap box with Kraft sticker Labels
2) Natural Olive Oil Based Bar Soap (labelling can be same as Organic but with distinct info)
3) Organic Hand Washes (clear square bottles, 250ml with natural pump)
4) Natural Olive Oil Based Body Wash (taper bottle 200ml with metal silver disc top caps)
I am a start up at home company making Organic and Natural Bar soaps, hand soaps, body washes.
All of my ingredients are organic or natural and will include natural essential oils, exfoliants, natural powders/colours, etc.
Some of the names are: Bramblix (feisty, energetic soap), Dusk (more of a sandalwood earthy tones with a sandalwood powder exfoliant), Tidal (maybe changing this name - fresh scented), Plum Basil (lemongrass/ginger, exfoliants), etc....
If you need more information, please let me know!
Please find attached: Kraft Paper I am looking at to possibly wrap the Bar Soaps in (I like the different colour concept and am trying to decide between diff colours of Wren Mabry paper to wrap around or plain kraft paper.. whichever the new logo concept will look best with.
The bottles I will be using for the hand soap (250ml square) and the body wash (200ml tapered)
OLD POST:
Hello! I am a start up business that is specializing in making luxury organic bar soaps, natural olive oil bar soaps, organic hand wash, natural olive oil body wash/shower gel that will include essential oils, exfoliants, natural powders, etc. (also accessories: wood soap dishes, etc) .. I am looking for a great designer that can provide me with the business card and labelling designs! I appreciate feedback, ideas on how I can receive a great design to help sell my products!
I am attaching my initial logo design that I would like to keep - but am looking for someone to 'finesse' it or make it more professional/unique looking.
Again, this is hand in hand with the business card project I submitted.
Thanks!
Odile
Updates
I am sorry for the lack of direction or Scope of the project. I am new at this board.
Labelling project:
I have attached an initial draft at a logo I tried to come up with for a business card and labelling/marketing. I am hoping that you can take this logo and 'run with it' to finesse it, make it look unique and professional.
If you need more information, please let me know.
Hello; I just wanted to let everyone know that if you feel that this brand needs a different logo, I am open to ideas (if you don't think the one I started with is ok). I am coming to the experts here!
Just to confirm also - this is related to the business card project, therefore, there are 2 projects, 2 payments! :)
Cheers

```html
<!DOCTYPE html>
<html lang="en">
<head>
<meta charset="utf-8">
<title>The Moss Hollow – Dusk Body Wash Label</title>
<link rel="stylesheet" href="https://fonts.googleapis.com/css2?family=Crimson+Pro:wght@400;600&display=swap">
<style>
  :root {
    --page-bg: #f4f3f0;
    --kraft: #a98c68;
    --kraft-light: #b39672;
    --kraft-dark: #9c7f5c;
    --ink: #2a2019;
    --brand-green: #2f3b22;
    --swatch: #d9773a;
    --rule: #4a3a2c;
    --pill: #2b2520;
    --pill-text: #f3ece2;
  }
  * { box-sizing: border-box; margin: 0; padding: 0; }
  html, body {
    width: 1052px;
    height: 1200px;
    overflow: hidden;
    background: var(--page-bg);
  }
  .canvas {
    position: relative;
    width: 1052px;
    height: 1200px;
  }
  .label {
    position: absolute;
    left: 276px;
    top: 50px;
    width: 500px;
    height: 1100px;
    background: radial-gradient(ellipse at 50% 40%, var(--kraft-light), var(--kraft) 60%, var(--kraft-dark));
    font-family: "Crimson Pro", Georgia, serif;
    color: var(--ink);
    text-align: center;
  }
  .label > * { position: absolute; }
  .brand-name,
  .brand-tagline {
    left: 0;
    right: 0;
    color: var(--brand-green);
    font-weight: 600;
  }
  .brand-name {
    top: 120px;
    font-size: 54px;
    line-height: 60px;
  }
  .brand-tagline {
    top: 196px;
    font-size: 19px;
    line-height: 28px;
    letter-spacing: 2px;
    text-transform: uppercase;
  }
  .brand-rule {
    left: 60px;
    right: 60px;
    top: 318px;
    height: 1px;
    background: rgba(60, 45, 30, 0.35);
    box-shadow: 0 2px 4px rgba(60, 45, 30, 0.25);
  }
  .product-base {
    left: 0;
    right: 0;
    top: 400px;
    font-size: 26px;
    line-height: 30px;
    font-weight: 600;
  }
  .product-type {
    left: 0;
    right: 0;
    top: 446px;
    font-size: 40px;
    line-height: 46px;
    font-weight: 600;
  }
  .scent-swatch {
    left: 234px;
    top: 513px;
    width: 44px;
    height: 46px;
    background: var(--swatch);
    border-radius: 3px;
  }
  .scent-name {
    left: 0;
    right: 0;
    top: 590px;
    font-size: 64px;
    line-height: 70px;
    font-weight: 600;
  }
  .scent-divider {
    left: 182px;
    top: 663px;
  }
  .scent-description {
    left: 0;
    right: 0;
    top: 705px;
    font-size: 24px;
    line-height: 36px;
  }
  .botanical {
    left: 89px;
    top: 842px;
    width: 333px;
    height: 112px;
    border-radius: 56px;
    background: radial-gradient(ellipse at 45% 55%, rgba(192, 85, 58, 0.55), rgba(111, 122, 78, 0.35) 55%, rgba(169, 140, 104, 0) 75%);
  }
  .volume {
    left: 213px;
    top: 1014px;
    width: 83px;
    height: 37px;
    border-radius: 11px;
    background: var(--pill);
    color: var(--pill-text);
    font-size: 21px;
    line-height: 37px;
  }
</style>
</head>
<body>
<div class="canvas">
  <section class="label">
    <div class="brand-name">The Moss Hollow</div>
    <div class="brand-tagline">Organic &amp; Natural Soaps</div>
    <div class="brand-rule"></div>

    <p class="product-base">Natural Olive Oil Based</p>
    <h1 class="product-type">Body Wash</h1>
    <div class="scent-swatch"></div>
    <h2 class="scent-name">Dusk</h2>
    <svg class="scent-divider" width="136" height="10" viewBox="0 0 136 10">
      <line x1="0" y1="5" x2="136" y2="5" stroke="var(--rule)" stroke-width="1.2"/>
      <rect x="64" y="1" width="8" height="8" transform="rotate(45 68 5)" fill="var(--rule)"/>
    </svg>
    <p class="scent-description">
      sandalwood earthy tones with<br>
      a sandalwood powder exfoliant<br>
      to smooth your skin
    </p>

    <div class="botanical" role="img" aria-label="Sprig of sandalwood leaves with red seeds"></div>

    <div class="volume">200 ml</div>
  </section>
</div>
</body>
</html>
```